Business Card for Multi-Brand Sportswear Company

We are looking for a business card which represents our company and the multiple brands within it.

The company: Fen Athletics (LTD)
The brands: Fen, TavaPuni, ElmStretch, Grit and Rain

Employees using these cards would be representing Fen Athletics, rather than any of the individual brands. You will see a current design within the uploaded files, to give some inspiration. The actual text of the brands is not necessary, but the logos should be on there is some format.

Our creative minds on this are stretched, so we are looking for someone to make this their own, and show us what a good business card should look like.

We may like to get these printed with spot gloss, so keep that in mind with your designs.

www.fenathletics.co.uk

Industry/Entity Type

Business

Contact Information for Business Card

Leo Pemberton-Hale
Operations Manager
(+44) 1632 960 418
Leo@fenathletics.co.uk
www.fenathletics.co.uk

Font styles to use
Sans Serif
Other font styles liked:
• Eurostile

Colors
ffffff

Requirements
Nice to have
• Dark (black) background

```html
<!DOCTYPE html>
<html lang="en">
<head>
<meta charset="utf-8">
<title>Fen Athletics – Business Card</title>
<link rel="stylesheet" href="https://fonts.googleapis.com/css2?family=Exo+2:wght@400;600;700&display=swap">
<style>
  :root {
    --backdrop: #3b3431;
    --card: #161616;
    --gloss: #2c2c2c;
    --band-light: #6d6d6d;
    --band-mid: #3a3a3a;
    --band-dark: #1c1c1c;
    --accent: #e2262b;
    --ink: #f2f2f2;
    --muted: #9a9a9a;
    --badge: #5b4c66;
  }
  * { box-sizing: border-box; margin: 0; padding: 0; }
  html, body { width: 1200px; height: 716px; overflow: hidden; }
  body {
    background: var(--backdrop);
    font-family: "Exo 2", "Helvetica Neue", Arial, sans-serif;
    position: relative;
  }
  .card {
    position: absolute;
    width: 520px;
    height: 297px;
    top: 210px;
    background: var(--card);
    border-radius: 3px;
    box-shadow: 0 6px 18px rgba(0,0,0,.45);
    overflow: hidden;
  }
  .card--front { left: 50px; }
  .card--back { left: 630px; }

  /* Front */
  .front-logo {
    position: absolute;
    left: 0; right: 0; top: 112px;
    text-align: center;
  }
  .front-logo__name {
    font-size: 40px;
    font-weight: 700;
    letter-spacing: 1px;
    color: var(--gloss);
    text-transform: uppercase;
  }
  .front-logo__tagline {
    margin-top: 4px;
    font-size: 10px;
    letter-spacing: 3px;
    color: var(--gloss);
    text-transform: uppercase;
  }

  /* Back */
  .header-band {
    position: absolute;
    left: 0; top: 26px;
    width: 520px; height: 46px;
    background: linear-gradient(90deg, var(--band-light) 0%, var(--band-mid) 55%, var(--band-dark) 100%);
  }
  .band-logo {
    position: absolute;
    right: 22px; top: 40px;
    text-align: right;
  }
  .band-logo__name {
    font-size: 17px;
    font-weight: 700;
    color: #0e0e0e;
    text-transform: uppercase;
    letter-spacing: .5px;
  }
  .band-logo__tagline {
    font-size: 6px;
    letter-spacing: 2px;
    color: #2a2a2a;
    text-transform: uppercase;
  }
  .holder { position: absolute; left: 26px; top: 82px; }
  .holder__name { font-size: 18px; font-weight: 700; color: var(--accent); }
  .holder__role { font-size: 11px; color: var(--ink); margin-top: 1px; }
  .contact-list {
    position: absolute; left: 26px; top: 150px;
    list-style: none;
    font-size: 12px; color: var(--ink);
  }
  .contact-list li { display: flex; align-items: center; height: 20px; }
  .contact-list svg { width: 11px; height: 11px; margin-right: 8px; fill: var(--accent); }
  .contact-list .web-name { color: var(--accent); }
  .contact-list .address { margin-top: 4px; }

  .brand-stack {
    position: absolute; right: 18px; bottom: 16px;
    list-style: none;
    display: flex; flex-direction: column; align-items: flex-end; gap: 9px;
    font-size: 11px; font-weight: 600; color: var(--ink);
  }
  .brand-stack li { display: flex; align-items: center; gap: 5px; }
  .brand-stack .dot { width: 10px; height: 10px; border-radius: 50%; border: 1.5px solid var(--muted); }
  .brand-stack .square { width: 10px; height: 10px; background: var(--badge); }
  .brand-stack .square--red { background: var(--accent); }
</style>
</head>
<body>
  <section class="card card--front" aria-label="Card front">
    <div class="front-logo">
      <div class="front-logo__name">Fen Athletics</div>
      <div class="front-logo__tagline">Performance Wear</div>
    </div>
  </section>

  <section class="card card--back" aria-label="Card back">
    <div class="header-band" role="img" aria-label="Decorative grey header band fading from light to dark"></div>
    <div class="band-logo">
      <div class="band-logo__name">Fen Athletics</div>
      <div class="band-logo__tagline">Performance Wear</div>
    </div>

    <div class="holder">
      <div class="holder__name">Leo Pemberton-Hale</div>
      <div class="holder__role">Operations Manager</div>
    </div>

    <ul class="contact-list">
      <li><svg viewBox="0 0 12 12"><path d="M2 1h3l1 3-1.5 1a6 6 0 0 0 2.5 2.5L8 6l3 1v3a1 1 0 0 1-1 1A9 9 0 0 1 1 2a1 1 0 0 1 1-1z"/></svg>+44 (0)1632 960418</li>
      <li><svg viewBox="0 0 12 12"><path d="M6 0a6 6 0 1 0 3 11.2l-.6-1A4.8 4.8 0 1 1 10.8 6v.6a1 1 0 0 1-2 0V3.5H7.7v.5A2.5 2.5 0 1 0 8.2 8 2.2 2.2 0 0 0 12 6.6V6a6 6 0 0 0-6-6zm0 4.6A1.4 1.4 0 1 1 6 7.4a1.4 1.4 0 0 1 0-2.8z"/></svg>leo@fenathletics.co.uk</li>
      <li><svg viewBox="0 0 12 12"><path d="M0 2h12v8H0zM1 3v.4l5 3.4 5-3.4V3z"/></svg>www.<span class="web-name">fenathletics</span>.co.uk</li>
      <li class="address">Marsh Lane, Elmfield, Wetherby, ZZ1 4QT</li>
    </ul>

    <ul class="brand-stack" aria-label="Group brands">
      <li>TavaPuni<span class="square"></span></li>
      <li>Grit and Rain<span class="square square--red"></span></li>
      <li>Fen</li>
      <li>ElmStretch<span class="dot"></span></li>
    </ul>
  </section>
</body>
</html>
```